Manifesto

I want a manifesto with the following five manifestos for our Not for Profit

- We are a For-purpose organisation
- Every service we offer is free
- Every product we sell funds our services
- Every financial transaction is transparent
- Our service is for the greater good
- Our purpose is always to serve the people
- We are a for purpose organisation

Its to go with this website logo/look/feel www.brightharbour.co.nz

Two attachments:

1. I quite like this look/feel of a manifesto (see attached), I want something clean, professional but I also quite like either Retro modern look feel also like a fresh, and uplifting as its for sick people coming to see us and our funds where anyone buys a product are used for helping those who are sick with healing......so needs something conveyed that is fresh, uplifing yet professional.
2. This attachment is how I wrote this down when inspired of how I wanted Bright Harbour to operate. This is our values chart. It has to say

Also check out our website for our logo, look etc.. it doesnt have to be the same but red somewhere would link back to logo. www.brightharbour.co.nz .

Industry/Entity Type

Financial

```html
<!DOCTYPE html>
<html lang="en">
<head>
<meta charset="utf-8">
<title>Bright Harbour Manifesto</title>
<link rel="stylesheet" href="https://fonts.googleapis.com/css2?family=Alfa+Slab+One&family=Architects+Daughter&family=Arvo:wght@700&family=Josefin+Slab:wght@300;400&family=Nunito:wght@800&family=Questrial&family=Zilla+Slab:wght@300&display=swap">
<style>
  :root {
    --paper: #ffffff;
    --panel: #e6e6e6;
    --ink: #111111;
    --ink-soft: #777777;
    --headword: #2b2b2b;
    --red: #ee1c1c;
    --deep-red: #b3241d;
    --teal: #17adad;
    --teal-deep: #0fb0b3;
    --aqua: #22e7ee;
    --aqua-pale: #6ef6f3;
    --lime: #8fe51c;
    --olive: #5f9a16;
  }
  html, body {
    margin: 0;
    padding: 0;
    width: 1200px;
    height: 848px;
    overflow: hidden;
    background: var(--paper);
  }
  .manifesto {
    display: block;
    width: 1200px;
    height: 848px;
  }
  .panel { fill: var(--panel); }

  .strapline {
    font-family: "Josefin Slab", serif;
    font-weight: 400;
    font-size: 31px;
    letter-spacing: 2.5px;
    fill: var(--ink-soft);
  }
  .brand-name {
    font-family: "Architects Daughter", cursive;
    font-size: 30px;
    fill: var(--red);
  }
  .brand-tag {
    font-family: "Questrial", sans-serif;
    font-size: 29px;
    fill: var(--ink);
  }
  .headword {
    font-family: "Alfa Slab One", serif;
    fill: var(--headword);
  }
  .light-sans {
    font-family: "Questrial", sans-serif;
    fill: var(--ink);
  }
  .light-slab {
    font-family: "Zilla Slab", serif;
    font-weight: 300;
    fill: var(--ink);
  }
  .hand {
    font-family: "Architects Daughter", cursive;
    fill: var(--ink);
  }
  .bold-sans {
    font-family: "Nunito", sans-serif;
    font-weight: 800;
    fill: var(--ink);
  }
  .bold-slab {
    font-family: "Arvo", serif;
    font-weight: 700;
    fill: var(--ink);
  }
  .url {
    font-family: "Questrial", sans-serif;
    font-size: 23px;
    letter-spacing: 1px;
    fill: var(--ink);
  }
  .word-free { fill: var(--red); }
  .word-funds { fill: var(--teal); }
  .word-services { fill: var(--aqua); }
  .word-is-green { fill: var(--olive); }
  .word-transparent { fill: var(--lime); }
  .word-the-aqua { fill: var(--aqua-pale); }
  .word-greater { fill: var(--aqua); }
  .word-good { fill: var(--teal-deep); }
  .word-the-red { fill: var(--red); }
  .word-people { fill: var(--deep-red); }
</style>
</head>
<body>
<svg class="manifesto" viewBox="0 0 1200 848" xmlns="http://www.w3.org/2000/svg" role="img" aria-label="Bright Harbour Manifesto">
  <rect class="panel" x="385" y="98" width="407" height="260"/>
  <rect class="panel" x="556" y="488" width="604" height="262"/>

  <text class="strapline" x="40" y="63" textLength="768" lengthAdjust="spacingAndGlyphs">WE ARE A FOR PURPOSE ORGANISATION</text>
  <text class="brand-name" x="1160" y="58" text-anchor="end">Bright Harbour</text>
  <text class="brand-tag" x="1160" y="90" text-anchor="end">Manifesto</text>

  <text class="headword" x="58" y="193" font-size="112" textLength="1084" lengthAdjust="spacingAndGlyphs">EVERY</text>

  <text class="light-sans" x="118" y="250" font-size="60" textLength="240" lengthAdjust="spacingAndGlyphs">service</text>
  <text class="hand" x="148" y="293" font-size="34" textLength="207" lengthAdjust="spacingAndGlyphs">we offer is</text>
  <text class="hand word-free" x="66" y="368" font-size="112" font-weight="700" textLength="290" lengthAdjust="spacingAndGlyphs">Free</text>

  <text class="bold-sans" x="430" y="242" font-size="42" textLength="190" lengthAdjust="spacingAndGlyphs">product</text>
  <text class="light-sans" x="630" y="258" font-size="38" textLength="130" lengthAdjust="spacingAndGlyphs">we sell</text>
  <text class="hand word-funds" x="432" y="305" font-size="60" textLength="198" lengthAdjust="spacingAndGlyphs">funds</text>
  <text class="hand word-services" x="485" y="347" font-size="40" textLength="280" lengthAdjust="spacingAndGlyphs">our services</text>

  <text class="light-slab" x="1160" y="256" font-size="58" text-anchor="end" textLength="270" lengthAdjust="spacingAndGlyphs">financial</text>
  <text class="light-slab" x="1160" y="314" font-size="58" text-anchor="end" textLength="320" lengthAdjust="spacingAndGlyphs">transaction</text>
  <text class="bold-slab word-is-green" x="1160" y="370" font-size="54" text-anchor="end">is</text>
  <text class="bold-slab word-transparent" x="596" y="428" font-size="80" textLength="562" lengthAdjust="spacingAndGlyphs">transparent</text>

  <text class="url" x="115" y="424" textLength="370" lengthAdjust="spacingAndGlyphs">www.brightharbour.co.nz</text>

  <text class="headword" x="42" y="528" font-size="84" textLength="538" lengthAdjust="spacingAndGlyphs">OUR</text>

  <text class="hand" x="42" y="585" font-size="36" textLength="258" lengthAdjust="spacingAndGlyphs">service is for</text>
  <text class="light-sans word-the-aqua" x="312" y="605" font-size="52" textLength="84" lengthAdjust="spacingAndGlyphs">the</text>
  <text class="light-sans word-greater" x="40" y="665" font-size="92" textLength="355" lengthAdjust="spacingAndGlyphs">greater</text>
  <text class="light-sans word-good" x="203" y="745" font-size="130" textLength="318" lengthAdjust="spacingAndGlyphs">good</text>

  <text class="light-slab" x="612" y="535" font-size="52" textLength="200" lengthAdjust="spacingAndGlyphs">purpose</text>
  <text class="light-slab" x="784" y="582" font-size="46">is</text>
  <text class="bold-slab" x="838" y="582" font-size="68" textLength="302" lengthAdjust="spacingAndGlyphs">always</text>
  <text class="hand" x="700" y="638" font-size="40" textLength="210" lengthAdjust="spacingAndGlyphs">to serve</text>
  <text class="bold-slab word-the-red" x="918" y="638" font-size="50" textLength="104" lengthAdjust="spacingAndGlyphs">the</text>
  <text class="bold-slab word-people" x="738" y="712" font-size="112" textLength="404" lengthAdjust="spacingAndGlyphs">people</text>

  <text class="strapline" x="393" y="806" textLength="765" lengthAdjust="spacingAndGlyphs">WE ARE A FOR PURPOSE ORGANISATION</text>
</svg>
</body>
</html>
```